BrivoTerna. Lantern of the Steady Harvest. Business card

Professional business card for BrivoTerna (Lantern of the Steady Harvest)
My rationale: Strategy-> Execution-> Results-> Value that lead to the BrivoTerna name: We put the Lantern of the Steady Harvest.
We deliver value to our customers helping them at defining a good strategy (cyan arrow). 90% of well formulated strategies fail due to poor execution so we also consider strategical execution very important (green arrow). Due to the execution we obtain the results (blue arrow). Finally, the results provide feedback to redefine strategy, and the new strategy has to be executed and new results obtained providing new feedback and on and on. It's like a wheel that finally, must create corporate value: value for shareholders, staholders, employees, providers...-

Target Market(s)

CEOs and steering comitees , invewrnent funds

Industry/Entity Type

Business Consultant

Contact Information for Business Card

Teodoro Vinsquel
CEO & Founder
teodoro.vinsquel@brivoterna-example.com
Mobile: +34 655.803.912
www.brivoterna-example.com

Colors

Designer to choose colors to be used in the design.

Requirements
Nice to have
• Nice to hace the words: Strategy, execution, results
• Nice to vave the claim: Lantern of the Steady Harvest
• The three colors should be shown:
• cyan for STRATEGY
• green for EXECUTION
• blue for RESULTS
Should not have
• Complete black background

```html
<!DOCTYPE html>
<html lang="en">
<head>
<meta charset="utf-8">
<title>BrivoTerna — Business Card</title>
<link rel="stylesheet" href="https://fonts.googleapis.com/css2?family=Montserrat:wght@400;500;700;800&display=swap">
<style>
  :root{
    --backdrop:#d3d3cf;
    --paper:#f1f0ee;
    --navy:#06339a;
    --cyan:#0aaeea;
    --green:#a6c75e;
    --ink:#3b3b3b;
    --charcoal:#2f2f2f;
    --charcoal-soft:#3c3c3c;
    --white:#ffffff;
  }
  *{margin:0;padding:0;box-sizing:border-box}
  html,body{width:1200px;height:801px;overflow:hidden}
  body{
    background:var(--backdrop);
    font-family:"Montserrat",sans-serif;
    display:flex;align-items:center;justify-content:center;gap:36px;
  }
  .card{
    position:relative;width:560px;height:320px;
    border-bottom:5px solid var(--cyan);
    box-shadow:0 14px 28px rgba(0,0,0,.18);
    overflow:hidden;
  }
  .card--front{background:var(--paper)}
  .card--back{background:var(--charcoal)}

  .wordmark{
    position:absolute;left:38px;top:120px;
    display:flex;align-items:center;gap:14px;
  }
  .wordmark__dot{width:18px;height:18px;border-radius:50%;background:var(--navy)}
  .wordmark__name{
    font-weight:800;font-size:52px;letter-spacing:-1px;color:var(--navy);line-height:1;
  }

  .person{position:absolute;left:38px;top:196px}
  .person__name{font-weight:700;font-size:19px;color:var(--cyan);line-height:1.1}
  .person__role{font-weight:400;font-size:12px;color:var(--ink);margin-top:3px}
  .person__rule{width:18px;height:2px;background:var(--green);margin:10px 0 7px}

  .contact{list-style:none}
  .contact__item{
    display:flex;align-items:center;gap:8px;
    font-size:11.5px;font-weight:500;color:var(--ink);line-height:17px;
  }
  .contact__icon{width:11px;height:11px;flex:none}

  .pattern{
    position:absolute;inset:0;
    background:linear-gradient(135deg,var(--charcoal) 0%,var(--charcoal-soft) 55%,var(--charcoal) 100%);
  }
  .back-mark{
    position:absolute;right:52px;bottom:96px;
    font-weight:800;font-size:16px;color:var(--white);letter-spacing:-.3px;
  }
</style>
</head>
<body>

  <section class="card card--front" aria-label="Business card front">
    <div class="wordmark">
      <span class="wordmark__dot"></span>
      <span class="wordmark__name">BrivoTerna</span>
    </div>

    <div class="person">
      <p class="person__name">Teodoro Vinsquel</p>
      <p class="person__role">CEO &amp; Founder</p>
      <div class="person__rule"></div>
      <ul class="contact">
        <li class="contact__item">
          <svg class="contact__icon" viewBox="0 0 12 12"><path d="M3 1 L5 3.5 L4 5 Q5 7 7 8 L8.5 7 L11 9 L9.5 11 Q4 10.5 1 3 Z" fill="var(--cyan)"/></svg>
          +34 655.803.912
        </li>
        <li class="contact__item">
          <svg class="contact__icon" viewBox="0 0 12 12"><rect x="1" y="2.5" width="10" height="7" fill="none" stroke="var(--cyan)" stroke-width="1.4"/><path d="M1 2.5 L6 7 L11 2.5" fill="none" stroke="var(--cyan)" stroke-width="1.4"/></svg>
          teodoro.vinsquel@brivoterna-example.com
        </li>
        <li class="contact__item">
          <svg class="contact__icon" viewBox="0 0 12 12"><circle cx="6" cy="6" r="5" fill="var(--cyan)"/><path d="M1 6 H11 M6 1 Q3 6 6 11 M6 1 Q9 6 6 11" fill="none" stroke="var(--paper)" stroke-width=".8"/></svg>
          www.brivoterna-example.com
        </li>
      </ul>
    </div>
  </section>

  <section class="card card--back" aria-label="Business card back">
    <div class="pattern" role="img" aria-label="Repeated faint brand symbol pattern on charcoal"></div>
    <span class="back-mark">BrivoTerna</span>
  </section>

</body>
</html>
```